One of Australia's fastest growing energy maintenance contractors needs a new website

www.brightleaf.com.au
Our business has evolved over the past years and now our website is no longer relevant.
We clean solar panels and we vacuum roof gutters.
We clean solar panels on the roofs of residential houses right up to billion dollar solar farms with in excess of 1 million panels. We offer thermal image testing and bird proofing for our residential and commercial clients and thermal drone imaging services for our solar farm clients.
We vacuum clean roof gutters (using a LoftSuck) on the residential house next door right up to enormous private and public schools, colleges, shopping centres, strat complexes and commercial buildings.
When first built our business had more of a domestic residential skew and the website reflected that. While that is still part of our core business we are now bidding on and have secured large government, commercial and infrastructure contracts and our new website needs to reflect our growth and our new business. We need a new site that it optimised for both desktop ad phone viewing as our latest figures showed that 73% of people visiting our site are on mobile phones. We have an extensive amount of data on Tallymark Insights available as well as Bidlines. Both that would also need integrating with the site along with a few other plugins such as Quilro Chat IQ, Chatterbox etc along with SEO key words etc. We are also the winner and finalists over multiple years of the small business of the year awards and we like to proudly and prominently display those on our site.
We are looking for a new site with a modern professional feel / theme
There is a definitive break in our business between the solar Panel cleaning clients and the gutter cleaning clients so we would like a home page that begins with a simple choice:
Solar Panel Cleaning – Gutter Cleaning
With a professional full screen background image (we have hundreds to choose from) and along the bottom a small area with rights reserved etc, phone number etc (at some point in the future we will split these into two businesses but for now it’s what we have).
After that selection is made we would like a repeat of that same scenario but the selection is:
If it’s Solar Panel Cleaning
(new background image)
Government – Infrastructure – Commercial – Residential
If it’s Gutter Cleaning
(new background image)
Government – Strata – Commercial – Residential
After making those choices then onto the relevant pages with background images relevant to each sector and a them that suits (on the residential we would like to keep the link to our tallymark reviews) - We will provide copy / text for each relevant page.
Other than that, a menu inclusive of the above and:
Resellers Portal – we will provide a link to this from Quilro CRM)
Customer portal (we will supply a link to this from our booking system)
We also need a page for our Solar Resellers / Partners page but we will give them a link to this, it won’t be listed on the site.
Request a quote page (Again we will provide information from Quilro as this will be linked to the CRM)
Standard contact us page inclusive of phone numbers, address and fields supplied from CRM
Sydney – 02 7391 8056
Southern Highlands – 02 4863 1708
Goulburn – 02 4863 1708
Canberra – 02 6172 4385
Wollongong – 02 4239 5817
sales@brightleaf.com.au
Head Office - Kelverton NSW 2590
ABN: 48093716552
Responsive Design: Optimized for desktop and mobile (73% mobile visitors).
Fast Loading Speed: Optimized for performance.
Smooth Transition Animations: For service and category selection.
Sticky Contact Bar: Always accessible at the bottom of mobile screens for quick calls.
SEO Optimization: Focused on government tenders, large-scale commercial contracts, and infrastructure projects.
Integrations
Tallymark Insights & Tallymark Bidlines.
Quilro Chat IQ.
Chatterbox Beacon.
SEO tools and keyword optimization.
Many many more images available if needed
Target Market(s)
Residential, commercial, Government

```html
<!DOCTYPE html>
<html lang="en">
<head>
<meta charset="utf-8">
<title>Brightleaf – Website Screens</title>
<link href="https://fonts.googleapis.com/css2?family=Lexend:wght@500;600&family=Roboto:wght@400;500;700&display=swap" rel="stylesheet">
<style>
  :root {
    --page-bg: #ffffff;
    --footer-bg: #111111;
    --brand-blue: #2a62b3;
    --icon-blue: #1f5aa6;
    --sky-deep: #1f7fcf;
    --sky-light: #62c6ef;
    --white: #ffffff;
    --divider: #4a4a4a;
    --muted: #d9d9d9;
  }
  * { box-sizing: border-box; margin: 0; padding: 0; }
  html, body {
    width: 1200px; height: 2812px; overflow: hidden;
    background: var(--page-bg);
    font-family: "Roboto", Arial, sans-serif;
    color: var(--white);
  }
  .stage {
    position: relative; width: 1100px; height: 2578px;
    transform: scale(1.0909); transform-origin: 0 0;
  }
  .screen { position: absolute; left: 65px; width: 969px; height: 785px; }
  .screen--home { top: 55px; }
  .screen--solar { top: 896px; }
  .screen--gutter { top: 1737px; }

  .hero { position: relative; height: 485px; overflow: hidden; }
  .hero__photo { position: absolute; inset: 0; }
  .hero__photo--home { background: radial-gradient(ellipse at 50% 20%, var(--sky-light) 0%, #3aa5e4 45%, var(--sky-deep) 100%); }
  .hero__photo--solar { background: linear-gradient(180deg, #5fa9d6 0%, #3f8fc6 55%, #2f7fbf 100%); }
  .hero__photo--gutter { background: linear-gradient(120deg, #3a7ea0 0%, #3f93c9 45%, #4aa3dc 100%); }

  .portal-links {
    position: absolute; top: 24px; right: 116px;
    font-size: 11px; font-weight: 700; display: flex; gap: 20px;
  }
  .brand-word { font-family: "Lexend", sans-serif; font-weight: 500; color: var(--white); }
  .brand-circle { position: absolute; border-radius: 50%; background: var(--white); }

  .home-brand__circle { left: 435px; top: 135px; width: 100px; height: 100px; }
  .home-brand__name { position: absolute; left: 0; right: 0; top: 250px; text-align: center; font-size: 46px; line-height: 56px; }

  .choice { position: absolute; top: 312px; height: 33px; display: flex; align-items: center; justify-content: center;
    font-size: 11px; font-weight: 500;
    clip-path: polygon(8% 0, 92% 0, 100% 50%, 92% 100%, 8% 100%, 0 50%); }
  .choice--solar { left: 323px; width: 158px; background: var(--white); }
  .choice--solar span { position: absolute; inset: 2px; display: flex; align-items: center; justify-content: center;
    background: var(--brand-blue); color: var(--white);
    clip-path: polygon(8% 0, 92% 0, 100% 50%, 92% 100%, 8% 100%, 0 50%); }
  .choice--gutter { left: 487px; width: 160px; background: var(--white); color: #333; }

  .corner-brand__circle { left: 158px; top: 18px; width: 46px; height: 46px; }
  .corner-brand__name { position: absolute; left: 114px; top: 78px; font-size: 22px; line-height: 26px; }

  .sector-title { position: absolute; left: 0; right: 0; top: 164px; text-align: center;
    font-family: "Lexend", sans-serif; font-weight: 600; font-size: 48px; line-height: 60px; }
  .sector { position: absolute; top: 234px; width: 114px; text-align: center; }
  .sector__hex { display: block; width: 114px; height: 124px; }
  .sector__label { position: absolute; left: -40px; right: -40px; top: 128px; font-size: 17px; font-weight: 700; line-height: 20px; }
  .sector--1 { left: 151px; } .sector--2 { left: 335px; } .sector--3 { left: 520px; } .sector--4 { left: 704px; }

  .site-footer { position: relative; height: 300px; background: var(--footer-bg); }
  .footer-brand__circle { left: 176px; top: 75px; width: 70px; height: 70px; }
  .footer-brand__name { position: absolute; left: 115px; top: 164px; font-size: 33px; line-height: 40px; }
  .footer-heading { position: absolute; top: 61px; font-size: 16px; font-weight: 700; line-height: 20px; }
  .footer-heading--phone { left: 338px; }
  .footer-heading--contact { left: 616px; }
  .icon-dot { position: absolute; width: 32px; height: 32px; border-radius: 50%; background: var(--brand-blue);
    display: flex; align-items: center; justify-content: center; }
  .icon-dot svg { width: 13px; height: 13px; }
  .icon-dot--phone { left: 340px; top: 90px; }
  .icon-dot--mail { left: 618px; top: 90px; }
  .icon-dot--pin { left: 618px; top: 135px; }
  .footer-lines { position: absolute; list-style: none; font-size: 12.5px; line-height: 22.6px; }
  .footer-lines--phone { left: 384px; top: 95px; }
  .footer-lines--contact { left: 662px; top: 95px; }
  .footer-lines--contact li:nth-child(2) { margin-top: 22.6px; }
  .footer-lines--contact li:nth-child(3) { margin-top: 22.6px; }
  .footer-divider { position: absolute; left: 115px; top: 239px; width: 738px; height: 1px; background: var(--divider); }
  .partners { position: absolute; left: 115px; top: 255px; display: flex; align-items: center; gap: 22px; font-size: 12px; color: var(--muted); }
  .partner { display: flex; align-items: center; gap: 5px; line-height: 20px; }
  .partner__dot { width: 9px; height: 9px; border-radius: 50%; background: var(--muted); }
  .copyright { position: absolute; right: 116px; top: 257px; font-size: 12.5px; line-height: 16px; }
</style>
</head>
<body>
<svg width="0" height="0" style="position:absolute" aria-hidden="true">
  <defs>
    <symbol id="hex" viewBox="0 0 114 124"><polygon points="57,0 114,31 114,93 57,124 0,93 0,31" fill="#ffffff"/></symbol>
    <symbol id="ic-government" viewBox="0 0 60 60"><g fill="none" stroke="currentColor" stroke-width="2" stroke-linejoin="round"><path d="M30 4v8M30 4h7v4h-7"/><path d="M16 24a14 12 0 0 1 28 0z"/><path d="M8 24h44v6H8z"/><path d="M12 30v18M20 30v18M28 30v18M36 30v18M44 30v18"/><path d="M6 48h48v6H6z"/></g></symbol>
    <symbol id="ic-infrastructure" viewBox="0 0 60 60"><g fill="none" stroke="currentColor" stroke-width="2" stroke-linejoin="round"><rect x="14" y="10" width="40" height="30" rx="2"/><path d="M28 40v8M40 40v8M22 52h24"/><circle cx="16" cy="36" r="8"/><circle cx="16" cy="36" r="3"/><path d="M24 20h20M24 26h14M34 4v6M42 4v6"/></g></symbol>
    <symbol id="ic-commercial" viewBox="0 0 60 60"><g fill="none" stroke="currentColor" stroke-width="2" stroke-linejoin="round"><path d="M6 54V20h14v34M20 54V8h18v46M38 54V22h16v32M2 54h56"/><path d="M10 26h6M10 34h6M10 42h6M25 14h8M25 22h8M25 30h8M25 38h8M43 28h6M43 36h6M43 44h6"/></g></symbol>
    <symbol id="ic-residential" viewBox="0 0 60 60"><g fill="none" stroke="currentColor" stroke-width="2" stroke-linejoin="round"><path d="M4 28 30 6l26 22"/><path d="M10 24v28h40V24"/><path d="M16 52V36h10v16M34 34h10v10H34zM39 34v10M34 39h10"/><path d="M14 16V8h6v4"/></g></symbol>
    <symbol id="ic-strata" viewBox="0 0 60 60"><g fill="none" stroke="currentColor" stroke-width="2" stroke-linejoin="round"><path d="M14 56 22 8l14 10v38M36 18l10 8v30M8 56h46"/><path d="M24 20v32M30 22v30M41 30v22"/></g></symbol>
    <symbol id="ic-phone" viewBox="0 0 16 16"><path fill="#fff" d="M3.6 1.5 5.8 1l1.1 3-1.4 1.1a8 8 0 0 0 4.4 4.4L11 8.1l3 1.1-.5 2.2c-.2.8-1 1.3-1.8 1.1C6.7 11.4 3.6 8.3 2.5 3.3c-.2-.8.3-1.6 1.1-1.8z"/></symbol>
    <symbol id="ic-mail" viewBox="0 0 16 16"><path fill="#fff" d="M1 3h14v10H1z"/><path fill="none" stroke="#2a62b3" stroke-width="1.4" d="M1.5 3.8 8 8.6l6.5-4.8"/></symbol>
    <symbol id="ic-pin" viewBox="0 0 16 16"><path fill="#fff" d="M8 1a5 5 0 0 1 5 5c0 3.6-5 9-5 9S3 9.6 3 6a5 5 0 0 1 5-5z"/><circle cx="8" cy="6" r="1.8" fill="#2a62b3"/></symbol>
  </defs>
</svg>

<main class="stage">

  <!-- Home: service choice -->
  <section class="screen screen--home">
    <div class="hero">
      <div class="hero__photo hero__photo--home" role="img" aria-label="Technician in safety gear washing rooftop solar panels with wind turbine behind, blue tinted"></div>
      <nav class="portal-links"><span>Resellers Portal</span><span>|</span><span>Customer portal</span></nav>
      <div class="brand-circle home-brand__circle"></div>
      <div class="brand-word home-brand__name">Brightleaf</div>
      <a class="choice choice--solar"><span>Solar Panel Cleaning</span></a>
      <a class="choice choice--gutter">Gutter Cleaning</a>
    </div>
    <footer class="site-footer">
      <div class="brand-circle footer-brand__circle"></div>
      <div class="brand-word footer-brand__name">Brightleaf</div>
      <h3 class="footer-heading footer-heading--phone">Phone</h3>
      <span class="icon-dot icon-dot--phone"><svg><use href="#ic-phone"/></svg></span>
      <ul class="footer-lines footer-lines--phone">
        <li>Sydney – 02 7391 8056</li><li>Southern Highlands – 02 4863 1708</li><li>Goulburn – 02 4863 1708</li><li>Canberra – 02 6172 4385</li><li>Wollongong – 02 4239 5817</li>
      </ul>
      <h3 class="footer-heading footer-heading--contact">Contact Info</h3>
      <span class="icon-dot icon-dot--mail"><svg><use href="#ic-mail"/></svg></span>
      <span class="icon-dot icon-dot--pin"><svg><use href="#ic-pin"/></svg></span>
      <ul class="footer-lines footer-lines--contact">
        <li>sales@brightleaf.com.au</li><li>Head Office - Kelverton NSW 2590</li><li>ABN: 48093716552</li>
      </ul>
      <div class="footer-divider"></div>
      <div class="partners">
        <span class="partner"><i class="partner__dot"></i>Quilro Chat IQ</span>
        <span class="partner">Tallymark Insights</span>
        <span class="partner">Tallymark Ads</span>
        <span class="partner">Find us on Chatterbox</span>
      </div>
      <p class="copyright">© Copyrights 2025 | All Rights Reserved</p>
    </footer>
  </section>

  <!-- Solar panel cleaning: sector choice -->
  <section class="screen screen--solar">
    <div class="hero">
      <div class="hero__photo hero__photo--solar" role="img" aria-label="Worker in hard hat and hi-vis vest cleaning a field of solar panels, blue tinted"></div>
      <div class="brand-circle corner-brand__circle"></div>
      <div class="brand-word corner-brand__name">Brightleaf</div>
      <nav class="portal-links"><span>Resellers Portal</span><span>|</span><span>Customer portal</span></nav>
      <h1 class="sector-title">Solar Panel Cleaning</h1>
      <a class="sector sector--1"><svg class="sector__hex" viewBox="0 0 114 124"><use href="#hex"/><use href="#ic-government" x="27" y="32" width="60" height="60" color="#1f5aa6"/></svg><span class="sector__label">Government</span></a>
      <a class="sector sector--2"><svg class="sector__hex" viewBox="0 0 114 124"><use href="#hex"/><use href="#ic-infrastructure" x="27" y="32" width="60" height="60" color="#1f5aa6"/></svg><span class="sector__label">Infrastructure</span></a>
      <a class="sector sector--3"><svg class="sector__hex" viewBox="0 0 114 124"><use href="#hex"/><use href="#ic-commercial" x="27" y="32" width="60" height="60" color="#1f5aa6"/></svg><span class="sector__label">Commercial</span></a>
      <a class="sector sector--4"><svg class="sector__hex" viewBox="0 0 114 124"><use href="#hex"/><use href="#ic-residential" x="27" y="32" width="60" height="60" color="#1f5aa6"/></svg><span class="sector__label">Residential</span></a>
    </div>
    <footer class="site-footer">
      <div class="brand-circle footer-brand__circle"></div>
      <div class="brand-word footer-brand__name">Brightleaf</div>
      <h3 class="footer-heading footer-heading--phone">Phone</h3>
      <span class="icon-dot icon-dot--phone"><svg><use href="#ic-phone"/></svg></span>
      <ul class="footer-lines footer-lines--phone">
        <li>Sydney – 02 7391 8056</li><li>Southern Highlands – 02 4863 1708</li><li>Goulburn – 02 4863 1708</li><li>Canberra – 02 6172 4385</li><li>Wollongong – 02 4239 5817</li>
      </ul>
      <h3 class="footer-heading footer-heading--contact">Contact Info</h3>
      <span class="icon-dot icon-dot--mail"><svg><use href="#ic-mail"/></svg></span>
      <span class="icon-dot icon-dot--pin"><svg><use href="#ic-pin"/></svg></span>
      <ul class="footer-lines footer-lines--contact">
        <li>sales@brightleaf.com.au</li><li>Head Office - Kelverton NSW 2590</li><li>ABN: 48093716552</li>
      </ul>
      <div class="footer-divider"></div>
      <div class="partners">
        <span class="partner"><i class="partner__dot"></i>Quilro Chat IQ</span>
        <span class="partner">Tallymark Insights</span>
        <span class="partner">Tallymark Ads</span>
        <span class="partner">Find us on Chatterbox</span>
      </div>
      <p class="copyright">© Copyrights 2025 | All Rights Reserved</p>
    </footer>
  </section>

  <!-- Gutter cleaning: sector choice -->
  <section class="screen screen--gutter">
    <div class="hero">
      <div class="hero__photo hero__photo--gutter" role="img" aria-label="Tradesman in checked shirt clearing leaves from a roof gutter on a tiled roof, blue tinted"></div>
      <div class="brand-circle corner-brand__circle"></div>
      <div class="brand-word corner-brand__name">Brightleaf</div>
      <nav class="portal-links"><span>Resellers Portal</span><span>|</span><span>Customer portal</span></nav>
      <h1 class="sector-title">Gutter Cleaning</h1>
      <a class="sector sector--1"><svg class="sector__hex" viewBox="0 0 114 124"><use href="#hex"/><use href="#ic-government" x="27" y="32" width="60" height="60" color="#1f5aa6"/></svg><span class="sector__label">Government</span></a>
      <a class="sector sector--2"><svg class="sector__hex" viewBox="0 0 114 124"><use href="#hex"/><use href="#ic-strata" x="27" y="32" width="60" height="60" color="#1f5aa6"/></svg><span class="sector__label">Strata</span></a>
      <a class="sector sector--3"><svg class="sector__hex" viewBox="0 0 114 124"><use href="#hex"/><use href="#ic-commercial" x="27" y="32" width="60" height="60" color="#1f5aa6"/></svg><span class="sector__label">Commercial</span></a>
      <a class="sector sector--4"><svg class="sector__hex" viewBox="0 0 114 124"><use href="#hex"/><use href="#ic-residential" x="27" y="32" width="60" height="60" color="#1f5aa6"/></svg><span class="sector__label">Residential</span></a>
    </div>
    <footer class="site-footer">
      <div class="brand-circle footer-brand__circle"></div>
      <div class="brand-word footer-brand__name">Brightleaf</div>
      <h3 class="footer-heading footer-heading--phone">Phone</h3>
      <span class="icon-dot icon-dot--phone"><svg><use href="#ic-phone"/></svg></span>
      <ul class="footer-lines footer-lines--phone">
        <li>Sydney – 02 7391 8056</li><li>Southern Highlands – 02 4863 1708</li><li>Goulburn – 02 4863 1708</li><li>Canberra – 02 6172 4385</li><li>Wollongong – 02 4239 5817</li>
      </ul>
      <h3 class="footer-heading footer-heading--contact">Contact Info</h3>
      <span class="icon-dot icon-dot--mail"><svg><use href="#ic-mail"/></svg></span>
      <span class="icon-dot icon-dot--pin"><svg><use href="#ic-pin"/></svg></span>
      <ul class="footer-lines footer-lines--contact">
        <li>sales@brightleaf.com.au</li><li>Head Office - Kelverton NSW 2590</li><li>ABN: 48093716552</li>
      </ul>
      <div class="footer-divider"></div>
      <div class="partners">
        <span class="partner"><i class="partner__dot"></i>Quilro Chat IQ</span>
        <span class="partner">Tallymark Insights</span>
        <span class="partner">Tallymark Ads</span>
        <span class="partner">Find us on Chatterbox</span>
      </div>
      <p class="copyright">© Copyrights 2025 | All Rights Reserved</p>
    </footer>
  </section>

</main>
</body>
</html>
```